Award-winnning Estate Agent needs a premium version of their 'For Sale' board design

We need a premium option for our 'For Sale' board design. We have a standard board that is attached to this brief, but were are looking to have a premium design version that we will use when selling exclusive properties. Our company name is Harbourline Vale Estates and the name for this is exclusive selection is: 'The Harbourline Collection'. The design needs to work with our current brand, but have a distinctive PREMIUM feel to it. I have uploaded the barnd guidelines and also some of the exisisting logo variations. We do NOT need a new logo but feel free to play around with colours, fonts, sizes etc. for the sign.

Target Market(s)

Property buyers & house hunters

Industry/Entity Type

Real Estate - Residential Property

Font styles to use
Sans Serif

Requirements
Must have
• A premium fee, must be square design, must be easy to read when driving past the sign
Nice to have
• I'm open ot ideas

```html
<!DOCTYPE html>
<html lang="en">
<head>
<meta charset="utf-8">
<title>Harbourline Vale Estates – For Sale Board</title>
<link rel="stylesheet" href="https://fonts.googleapis.com/css2?family=Bebas+Neue&family=Montserrat:wght@700;800&family=Inter:wght@600&display=swap">
<style>
  :root {
    --backdrop: #dcdcdc;
    --board-white: #ffffff;
    --brand-blue: #426aa8;
    --accent-blue: #5ba4d0;
    --brand-purple: #432c74;
    --ink: #111111;
    --rule-grey: #8a8a8a;
  }
  html, body {
    margin: 0;
    padding: 0;
    width: 974px;
    height: 1200px;
    overflow: hidden;
    background: var(--backdrop);
  }
  .board {
    position: absolute;
    left: 77px;
    top: 190px;
    width: 820px;
    height: 820px;
    box-shadow: 0 10px 30px rgba(0,0,0,0.22);
    background: var(--board-white);
  }
  .board svg { display: block; width: 100%; height: 100%; }
  .brand-name { font-family: "Inter", sans-serif; font-weight: 600; fill: var(--brand-purple); }
  .headline { font-family: "Bebas Neue", sans-serif; fill: var(--brand-blue); }
  .collection-top { font-family: "Montserrat", sans-serif; font-weight: 800; fill: var(--brand-purple); }
  .collection-bottom { font-family: "Montserrat", sans-serif; font-weight: 800; fill: var(--ink); }
  .phone-number { font-family: "Montserrat", sans-serif; font-weight: 700; fill: var(--board-white); }
  .web-address { font-family: "Montserrat", sans-serif; font-weight: 700; fill: var(--board-white); }
</style>
</head>
<body>
  <div class="board">
    <svg viewBox="0 0 1000 1000" xmlns="http://www.w3.org/2000/svg">
      <rect class="board-face" width="1000" height="1000" fill="var(--board-white)"/>

      <!-- brand mark -->
      <rect class="brand-square" x="455" y="110" width="90" height="90" fill="var(--accent-blue)"/>
      <text class="brand-name" x="500" y="258" font-size="46" text-anchor="middle">Harbourline Vale Estates</text>

      <!-- headline -->
      <text class="headline" x="500" y="507" font-size="286" text-anchor="middle" textLength="785" lengthAdjust="spacingAndGlyphs">FOR SALE</text>

      <!-- divider -->
      <line class="divider" x1="102" y1="532" x2="900" y2="532" stroke="var(--rule-grey)" stroke-width="1.5"/>
      <rect class="divider-accent" x="420" y="528" width="161" height="9" rx="4.5" fill="var(--accent-blue)"/>

      <!-- collection title -->
      <text class="collection-top" x="500" y="617" font-size="64" text-anchor="middle" textLength="640" lengthAdjust="spacingAndGlyphs">THE HARBOURLINE</text>
      <text class="collection-bottom" x="500" y="682" font-size="66" text-anchor="middle" textLength="440" lengthAdjust="spacingAndGlyphs">COLLECTION</text>

      <!-- swoosh bands -->
      <path class="swoosh-blue" d="M0 598 C200 700 450 748 730 750 C450 758 200 738 0 688 Z" fill="var(--brand-blue)"/>
      <path class="contact-band" d="M0 700 C300 792 700 792 1000 700 L1000 1000 L0 1000 Z" fill="var(--brand-purple)"/>

      <!-- phone -->
      <g class="phone-icon" transform="translate(182 820)">
        <path d="M8 4 C14 0 20 2 22 8 L26 18 C27 22 25 25 22 27 L18 30 C22 40 30 48 40 52 L43 48 C45 45 48 44 52 45 L62 49 C67 51 69 57 66 62 L62 68 C58 72 50 72 40 67 C24 59 11 46 3 30 C-2 20 -1 10 8 4 Z" fill="var(--accent-blue)"/>
        <path d="M38 22 A12 12 0 0 1 48 32 M38 12 A22 22 0 0 1 58 32" stroke="var(--accent-blue)" stroke-width="3.5" fill="none" stroke-linecap="round"/>
      </g>
      <text class="phone-number" x="255" y="875" font-size="78" textLength="565" lengthAdjust="spacing">01632 960418</text>
      <text class="web-address" x="500" y="932" font-size="38" text-anchor="middle" textLength="690" lengthAdjust="spacingAndGlyphs">www.harbourlinevaleestates.co.uk</text>
    </svg>
  </div>
</body>
</html>
```